Birchvale Gundogs

create website page for Labrador Retriever stud dog business.

Target Market(s)

Owners looking to breed their dogs that compete in NFS/PTL hunt tests.

Industry/Entity Type

Dog Training

Logo Text

Birchvale Gundogs - Stud Dogs

Number of Pages Required

1 page

Colors

Designer to choose colors to be used in the design.

Requirements
Must have
• link to or info from my dogs pedigree.
• Main dog I'm advertising. GRCH Zeke's Jump 5 Rounds FX
• http://www.fieldpuplineage.example/lineage.asp?id=71926
• also link to gundog tallies-- for pass information.
• Can update the pictures to that actual pictures once design is complete.

```html
<!DOCTYPE html>
<html lang="en">
<head>
<meta charset="utf-8">
<title>Birchvale Gundogs – Stud Dogs</title>
<link rel="stylesheet" href="https://fonts.googleapis.com/css2?family=Montserrat:wght@400;500;600;700&family=Roboto:wght@400;500&family=Open+Sans:wght@400;600&display=swap">
<style>
:root{
  --blue:#0b78ab;
  --blue-dark:#0a6a98;
  --gold:#de9a05;
  --ink:#3a3a3a;
  --muted:#555;
  --line:#e2e2e2;
  --panel:#f2f2f2;
  --white:#fff;
}
*{box-sizing:border-box;margin:0;padding:0}
html,body{width:1200px;height:2844px;overflow:hidden}
body{position:relative;background:var(--white);font-family:"Open Sans",Arial,sans-serif;color:var(--ink)}
.abs{position:absolute}

/* header */
.site-header{position:absolute;left:0;top:0;width:1200px;height:100px;background:var(--white)}
.brand{position:absolute;left:85px;top:38px;font-family:"Montserrat",sans-serif;font-weight:500;font-size:27px;letter-spacing:.5px;color:var(--blue)}
.auth-btn{position:absolute;top:15px;height:36px;line-height:36px;text-align:center;color:var(--white);font-family:"Roboto",sans-serif;font-weight:500;font-size:13px}
.auth-login{left:933px;width:77px;background:var(--gold)}
.auth-signup{left:1026px;width:87px;background:var(--blue)}
.main-nav a{position:absolute;top:70px;font-family:"Roboto",sans-serif;font-size:12px;font-weight:500;color:#333;text-decoration:none}
.main-nav a.active{color:var(--gold)}

/* hero */
.hero{position:absolute;left:0;top:100px;width:1200px;height:596px;background:linear-gradient(160deg,#5f6b2a 0%,#8a7a35 35%,#a88a40 55%,#6d5a33 75%,#4a3b26 100%)}
.hero-arrow{position:absolute;top:370px;width:54px;height:54px}
.hero-title{position:absolute;right:87px;top:438px;text-align:right;color:var(--white);font-family:"Montserrat",sans-serif}
.hero-title h1{font-size:30px;font-weight:500;letter-spacing:.5px}
.hero-title p{font-size:16px;font-weight:500;margin-top:10px}

/* search */
.search-band{position:absolute;left:0;top:696px;width:1200px;height:121px;background:var(--gold)}
.search-label{position:absolute;left:97px;top:41px;color:var(--white);font-family:"Montserrat",sans-serif;font-weight:500;font-size:26px}
.search-field{position:absolute;top:42px;height:39px;background:var(--white);font-family:"Roboto",sans-serif;font-size:12px;color:#555;line-height:39px;padding-left:14px}
.search-name{left:377px;width:277px}
.search-breed{left:660px;width:277px}
.search-submit{position:absolute;left:942px;top:42px;width:158px;height:39px;background:var(--blue);color:var(--white);text-align:center;line-height:39px;font-family:"Roboto",sans-serif;font-weight:500;font-size:14px}

/* welcome */
.welcome-photo{position:absolute;left:57px;top:834px;width:493px;height:342px;background:radial-gradient(ellipse at 50% 55%,#e4b58a 0%,#d9a574 35%,#f6efe8 70%,#fff 100%)}
.section-title{font-family:"Montserrat",sans-serif;font-weight:600;color:var(--blue);text-transform:uppercase}
.welcome-title{position:absolute;left:576px;top:875px;font-size:21px}
.welcome-copy{position:absolute;left:576px;top:936px;width:537px;font-size:11.6px;line-height:25px;color:var(--muted)}
.welcome-copy p+p{margin-top:25px}
.btn-blue{position:absolute;background:var(--blue);color:var(--white);text-align:center;font-family:"Montserrat",sans-serif;font-weight:600;font-size:13px;text-transform:uppercase}
.read-more{left:574px;top:1168px;width:158px;height:47px;line-height:47px}

/* featured */
.featured{position:absolute;left:0;top:1270px;width:1200px;height:546px;background:var(--panel)}
.centered-title{position:absolute;left:0;width:1200px;text-align:center;font-size:26px}
.centered-sub{position:absolute;left:0;width:1200px;text-align:center;font-size:11.5px;color:var(--muted)}
.dog-card{position:absolute;top:226px;width:247px;height:250px;background:var(--white);text-align:center}
.dog-photo{position:absolute;left:39px;top:-72px;width:170px;height:170px;border-radius:50%;border:4px solid var(--white);box-shadow:0 0 0 1px #ddd}
.dog-card h3{position:absolute;left:0;top:118px;width:100%;font-family:"Montserrat",sans-serif;font-weight:600;font-size:14px;color:var(--gold)}
.dog-card p{position:absolute;left:20px;top:150px;width:207px;font-size:11.5px;line-height:21px;color:var(--muted)}
.pager-dot{position:absolute;top:510px;width:12px;height:12px;border-radius:50%;background:#8a8a8a}
.pager-dot.on{background:var(--gold)}

/* faq */
.faq-item{position:absolute;left:209px;width:781px;background:#f7f7f7;border:1px solid var(--line);font-family:"Open Sans",sans-serif;font-size:11.5px;color:#666;text-transform:uppercase}
.faq-q{position:absolute;left:40px;top:16px}
.faq-icon{position:absolute;left:15px;top:15px;width:17px;height:17px}
.faq-item.open .faq-q{color:var(--gold);font-weight:600}
.faq-a{position:absolute;left:40px;top:52px;width:710px;text-transform:none;color:#555;line-height:22px;font-size:11.5px}
.view-more{left:512px;top:2271px;width:176px;height:46px;line-height:46px}

/* newsletter */
.newsletter{position:absolute;left:0;top:2347px;width:1200px;height:260px;background:var(--gold);text-align:center;color:var(--white)}
.newsletter h2{position:absolute;left:0;top:40px;width:100%;font-family:"Montserrat",sans-serif;font-weight:500;font-size:26px}
.newsletter p{position:absolute;left:240px;top:92px;width:720px;font-size:11.5px;line-height:24px}
.news-input{position:absolute;left:286px;top:165px;width:482px;height:49px;background:var(--white);color:#555;font-size:12px;line-height:49px;text-align:left;padding-left:16px}
.news-submit{position:absolute;left:768px;top:165px;width:148px;height:49px;line-height:49px;background:var(--blue);font-family:"Montserrat",sans-serif;font-weight:600;font-size:14px}

/* footer */
.site-footer{position:absolute;left:0;top:2607px;width:1200px;height:237px;background:var(--blue)}
.social{position:absolute;top:34px;width:60px;height:60px;border:1.5px solid rgba(255,255,255,.75);border-radius:50%}
.footer-nav{position:absolute;left:0;top:132px;width:1200px;text-align:center;font-family:"Roboto",sans-serif;font-size:11.5px;color:var(--white)}
.footer-nav span{margin:0 26px}
.copyright{position:absolute;left:0;top:176px;width:1200px;text-align:center;font-size:11px;color:#dfeef6}
</style>
</head>
<body>

<header class="site-header">
  <div class="brand">Birchvale Gundogs</div>
  <div class="auth-btn auth-login">LOGIN</div>
  <div class="auth-btn auth-signup">SIGN UP</div>
  <nav class="main-nav">
    <a class="active" style="left:519px">HOME</a>
    <a style="left:595px">ABOUT US</a>
    <a style="left:694px">SERVICES</a>
    <a style="left:790px">FEATURES</a>
    <a style="left:889px">FAQ'S</a>
    <a style="left:963px">NEWS</a>
    <a style="left:1039px">CONTACT US</a>
  </nav>
</header>

<section class="hero" role="img" aria-label="Photo of a yellow Labrador retriever lying on a log under autumn trees">
  <svg class="hero-arrow" style="left:24px" viewBox="0 0 54 54"><circle cx="27" cy="27" r="25" fill="none" stroke="#fff" stroke-width="2"/><path d="M31 17 L21 27 L31 37" fill="none" stroke="#fff" stroke-width="3"/></svg>
  <svg class="hero-arrow" style="left:1120px" viewBox="0 0 54 54"><circle cx="27" cy="27" r="25" fill="none" stroke="#fff" stroke-width="2"/><path d="M23 17 L33 27 L23 37" fill="none" stroke="#fff" stroke-width="3"/></svg>
  <div class="hero-title">
    <h1>BIRCHVALE GUNDOGS</h1>
    <p>WE ARE INTO LABRADOR RETRIEVER STUD DOG BUSINESS</p>
  </div>
</section>

<section class="search-band">
  <div class="search-label">SEARCH/ADD DOG :</div>
  <div class="search-field search-name">Full or part Registered Name :</div>
  <div class="search-field search-breed">Breed:
    <svg class="abs" style="right:12px;top:17px" width="9" height="5" viewBox="0 0 9 5"><path d="M0 0H9L4.5 5Z" fill="#555"/></svg>
  </div>
  <div class="search-submit">SUBMIT</div>
</section>

<div class="welcome-photo" role="img" aria-label="Photo of three Labrador puppies sitting side by side"></div>
<h2 class="section-title welcome-title">Welcome to Birchvale Gundogs</h2>
<div class="welcome-copy">
  <p>Sed ut perspiciatis unde omnis iste natus error sit voluptatem accusantium doloremque laudantium, totam rem aperiam, eaque ipsa quae ab illo inventore veritatis et quasi architecto beatae vitae dicta sunt explicabo. Nemo enim ipsam voluptatem quia voluptas sit aspernatur aut odit aut fugit, sed quia consequuntur magni dolores eos qui ratione voluptatem sequi nesciunt.</p>
  <p>Eaque ipsa quae ab illo inventore veritatis et quasi architecto beatae vitae dicta sunt explicabo Nemo enim ipsam voluptatem quia voluptas sit aspernatur aut odit aut fugit, sed quia consequuntur magni dolores eos qui ratione voluptatem sequi nesciunt.</p>
</div>
<div class="btn-blue read-more">Read More Info</div>

<section class="featured">
  <h2 class="section-title centered-title" style="top:46px">Featured Dog</h2>
  <p class="centered-sub" style="top:94px">Sed ut perspiciatis unde omnis iste natus error sit voluptatem accusantium doloremque laudantium, totam rem aperiam, eaque</p>

  <article class="dog-card" style="left:85px">
    <div class="dog-photo" role="img" aria-label="Photo of a black Labrador splashing through water" style="background:radial-gradient(circle,#7a8a8c,#3d4446)"></div>
    <h3>CONTRARY TO POPULAR</h3>
    <p>Sed ut perspiciatis unde omnis iste nat us error sit voluptatem accusantium vit ae dicta sunt explicabo.</p>
  </article>
  <article class="dog-card" style="left:347px">
    <div class="dog-photo" role="img" aria-label="Portrait photo of a black Labrador" style="background:radial-gradient(circle,#2a2a2a 40%,#d9b46a)"></div>
    <h3>CONTRARY TO POPULAR</h3>
    <p>Sed ut perspiciatis unde omnis iste nat us error sit voluptatem accusantium vit ae dicta sunt explicabo.</p>
  </article>
  <article class="dog-card" style="left:609px">
    <div class="dog-photo" role="img" aria-label="Photo of a black Labrador retrieving a game bird" style="background:radial-gradient(circle,#6a4a30,#2c2a2a)"></div>
    <h3>CONTRARY TO POPULAR</h3>
    <p>Sed ut perspiciatis unde omnis iste nat us error sit voluptatem accusantium vit ae dicta sunt explicabo.</p>
  </article>
  <article class="dog-card" style="left:868px">
    <div class="dog-photo" role="img" aria-label="Photo of a black Labrador carrying a retrieve through water" style="background:radial-gradient(circle,#8a9aa6,#4a5560)"></div>
    <h3>CONTRARY TO POPULAR</h3>
    <p>Sed ut perspiciatis unde omnis iste nat us error sit voluptatem accusantium vit ae dicta sunt explicabo.</p>
  </article>

  <span class="pager-dot" style="left:576px"></span>
  <span class="pager-dot on" style="left:593px"></span>
  <span class="pager-dot" style="left:610px"></span>
</section>

<h2 class="section-title centered-title" style="top:1849px">Our FAQ's</h2>
<p class="centered-sub" style="top:1896px">Sed ut perspiciatis unde omnis iste natus error sit voluptatem accusantium doloremque laudantium, totam rem aperiam, eaque</p>

<div class="faq-item" style="top:1953px;height:49px">
  <svg class="faq-icon" viewBox="0 0 17 17"><circle cx="8.5" cy="8.5" r="8" fill="#888"/><path d="M8.5 4.5V12.5M4.5 8.5H12.5" stroke="#fff" stroke-width="2"/></svg>
  <span class="faq-q">What's the purpose of Birchvale Gundogs?</span>
</div>
<div class="faq-item open" style="top:2012px;height:117px">
  <svg class="faq-icon" viewBox="0 0 17 17"><circle cx="8.5" cy="8.5" r="8" fill="#de9a05"/><path d="M4.5 8.5H12.5" stroke="#fff" stroke-width="2"/></svg>
  <span class="faq-q">Why are their only certain breeds on this site?</span>
  <p class="faq-a">Sed ut perspiciatis unde omnis iste natus error sit voluptatem accusantium doloremque laudantium, totam rem aperiam, eaque ipsa quae ab illo inventore veritatis et quasi architecto beatae vitae dicta sunt explicabo.</p>
</div>
<div class="faq-item" style="top:2137px;height:49px">
  <svg class="faq-icon" viewBox="0 0 17 17"><circle cx="8.5" cy="8.5" r="8" fill="#888"/><path d="M8.5 4.5V12.5M4.5 8.5H12.5" stroke="#fff" stroke-width="2"/></svg>
  <span class="faq-q">May I add my Birchvale Gundogs?</span>
</div>
<div class="faq-item" style="top:2192px;height:49px">
  <svg class="faq-icon" viewBox="0 0 17 17"><circle cx="8.5" cy="8.5" r="8" fill="#888"/><path d="M8.5 4.5V12.5M4.5 8.5H12.5" stroke="#fff" stroke-width="2"/></svg>
  <span class="faq-q">Can I edit someone else's dog?</span>
</div>
<div class="btn-blue view-more">View More</div>

<section class="newsletter">
  <h2>NEWSLETTER SIGNUP</h2>
  <p>Sed ut perspiciatis unde omnis iste natus error sit voluptatem accusantium doloremque laudantium, totam rem aperiam, eaque ipsa quae ab illo inventore veritatis et quasi architecto beatae vitae dicta sunt explicabo.</p>
  <div class="news-input">Enter Your Email id :</div>
  <div class="news-submit">SUBSCRIBE</div>
</section>

<footer class="site-footer">
  <span class="social" style="left:391px" aria-label="Social link"></span>
  <span class="social" style="left:463px" aria-label="Social link"></span>
  <span class="social" style="left:533px" aria-label="Social link"></span>
  <span class="social" style="left:605px" aria-label="Social link"></span>
  <span class="social" style="left:675px" aria-label="Social link"></span>
  <span class="social" style="left:747px" aria-label="Email">
    <svg class="abs" style="left:19px;top:21px" width="20" height="15" viewBox="0 0 20 15"><rect x="1" y="1" width="18" height="13" fill="none" stroke="#fff" stroke-width="1.8"/><path d="M1 1L10 8L19 1" fill="none" stroke="#fff" stroke-width="1.8"/></svg>
  </span>
  <nav class="footer-nav">
    HOME<span>|</span>ABOUT US<span>|</span>SERVICES<span>|</span>FEATURES<span>|</span>FAQ'S<span>|</span>NEWS<span>|</span>CONTACT US
  </nav>
  <p class="copyright">© Copyrights 2017 Birchvale Gundogs.All Rights Reserved.</p>
</footer>

</body>
</html>
```